Allied Health team of Physiotherapists & Occupational Therapists seek a business card design

We have our new logo, we now need our new business cards and stationary. Tidewell: Oedema & Family Clinic is seeking a generic card design to represent our whole team and individual cards for each therapist that incorporates our new logo to communicate our holistic approach that is calming, nuturing, supportive and welcoming.
Our Physiotherapists and Occupational Therapists assess, treat and provide education for people who are at risk of or who have lymphoedema. This is often as a result of treatment for cancer. We provide pre-operative and post-operative management and cancer rehabilitation in our Pilates studio. Our team also consists of Physiotherapists who have a strong interest in pelvic floor and continence management for both men and women.

Target Market(s)

Mainly women health conscious

Industry/Entity Type

Allied Health: Physiotherapy / Occupational Therapy

Contact Information for Business Card

Address: 14 Gallivant Ave Frankston 3199 Phone: 84316570 fax: 8431 6578 Email: info@tidewellcareservices.com.au Website: tidewellcareservices.com.au Facebook address: facebook.com/TidewellOedemaAndFamilyCareClinic. Room to write appointments. Individual cards need to have name, office email and individual email and professional details

Requirements
Must have
• Logo as per uploaded documents

```html
<!DOCTYPE html>
<html lang="en">
<head>
<meta charset="utf-8">
<title>Tidewell Business Card</title>
<link href="https://fonts.googleapis.com/css2?family=Oswald:wght@400;500&family=Open+Sans:wght@400;600&display=swap" rel="stylesheet">
<style>
  :root {
    --peach: #f9b083;
    --green: #077845;
    --white: #ffffff;
    --stage: #ecebe8;
    --ink-on-peach: #ffffff;
  }
  * { margin: 0; padding: 0; box-sizing: border-box; }
  html, body {
    width: 1200px;
    height: 900px;
    overflow: hidden;
    background: var(--stage);
  }
  .card {
    position: absolute;
    left: 100px;
    top: 142px;
    width: 1000px;
    height: 617px;
    background: var(--green);
    overflow: hidden;
    box-shadow: 0 10px 30px rgba(0,0,0,0.15);
  }
  .card__peach {
    position: absolute;
    left: 0; top: 0;
    width: 676px;
    height: 100%;
    background: var(--peach);
  }
  .card__disc {
    position: absolute;
    left: 411px;
    top: 41px;
    width: 534px;
    height: 534px;
    border-radius: 50%;
    background: var(--white);
    display: flex;
    align-items: center;
    justify-content: center;
  }
  .brand-name {
    width: 300px;
    text-align: center;
    font-family: "Open Sans", sans-serif;
    font-weight: 600;
    font-size: 27px;
    line-height: 1.35;
    color: var(--peach);
  }
  .person {
    position: absolute;
    left: 47px;
    top: 122px;
    color: var(--ink-on-peach);
  }
  .person__name {
    font-family: "Oswald", sans-serif;
    font-weight: 500;
    font-size: 38px;
    letter-spacing: 2px;
    line-height: 1;
  }
  .person__role {
    font-family: "Open Sans", sans-serif;
    font-size: 13px;
    margin-top: 8px;
  }
  .address {
    position: absolute;
    left: 47px;
    top: 222px;
    font-family: "Open Sans", sans-serif;
    font-size: 17px;
    line-height: 25px;
    color: var(--ink-on-peach);
  }
  .contacts {
    position: absolute;
    left: 47px;
    top: 349px;
    list-style: none;
  }
  .contact {
    display: flex;
    align-items: center;
    height: 25px;
    margin-bottom: 13px;
    font-family: "Open Sans", sans-serif;
    font-size: 19px;
    color: var(--ink-on-peach);
  }
  .contact__icon {
    width: 25px;
    height: 25px;
    margin-right: 22px;
    flex-shrink: 0;
  }
  .contact--web { font-size: 16px; }
</style>
</head>
<body>
  <div class="card">
    <div class="card__peach"></div>

    <div class="person">
      <div class="person__name">MAREN HOLLOWAY</div>
      <div class="person__role">CEO/Managing Director</div>
    </div>

    <div class="address">
      370 Halcyon Avenue NW<br>
      Suite 210.Fernhill<br>
      Mi 40917
    </div>

    <ul class="contacts">
      <li class="contact">
        <svg class="contact__icon" viewBox="0 0 25 25" aria-hidden="true">
          <rect width="25" height="25" rx="5" fill="#fff"/>
          <path d="M8 5.5l2.5 3.5-1.5 1.5c.8 2 2.5 3.7 4.5 4.5l1.5-1.5 3.5 2.5-1.5 2.5c-5 .5-11-5.5-10.5-10.5z" fill="none" stroke="#f9b083" stroke-width="1.6" stroke-linejoin="round"/>
        </svg>
        318-004-5176
      </li>
      <li class="contact">
        <svg class="contact__icon" viewBox="0 0 25 25" aria-hidden="true">
          <rect width="25" height="25" rx="5" fill="#fff"/>
          <rect x="8" y="4.5" width="9" height="5" fill="none" stroke="#f9b083" stroke-width="1.5"/>
          <rect x="5" y="9.5" width="15" height="8" rx="1" fill="none" stroke="#f9b083" stroke-width="1.5"/>
          <rect x="8" y="14" width="9" height="6.5" fill="#fff" stroke="#f9b083" stroke-width="1.5"/>
        </svg>
        318-004-5176
      </li>
      <li class="contact">
        <svg class="contact__icon" viewBox="0 0 25 25" aria-hidden="true">
          <rect x="1" y="4" width="23" height="17" fill="none" stroke="#fff" stroke-width="1.6"/>
          <path d="M1 4l11.5 9L24 4" fill="none" stroke="#fff" stroke-width="1.6"/>
        </svg>
        Marenholloway@mailplace.com
      </li>
      <li class="contact contact--web">
        <svg class="contact__icon" viewBox="0 0 25 25" aria-hidden="true">
          <rect width="25" height="25" rx="5" fill="#fff"/>
          <circle cx="12.5" cy="12.5" r="7" fill="none" stroke="#f9b083" stroke-width="1.5"/>
          <ellipse cx="12.5" cy="12.5" rx="3" ry="7" fill="none" stroke="#f9b083" stroke-width="1.2"/>
          <path d="M5.5 12.5h14M6.5 9h12M6.5 16h12" stroke="#f9b083" stroke-width="1.2"/>
        </svg>
        www.carevoyage.com
      </li>
    </ul>

    <div class="card__disc">
      <div class="brand-name">Tidewell: Oedema &amp; Family Clinic</div>
    </div>
  </div>
</body>
</html>
```